Business card design for my company.
I would like the card's background colour to be black. You can also see our web site to get an idea of our brand. https://www.tmwhomecrafting.com.au/
- Name
- Email

```html
<!DOCTYPE html>
<html lang="en">
<head>
<meta charset="utf-8">
<title>TMW Home Crafting – Business Card</title>
<link rel="stylesheet" href="https://fonts.googleapis.com/css2?family=Montserrat:wght@400;600&display=swap">
<style>
  :root {
    --page-bg: #e9e6e2;
    --card-black: #0b0b0b;
    --card-charcoal: #2e2e2e;
    --brand-green: #0f7a34;
    --brand-green-light: #2f9a55;
    --silver: #d9d9d6;
    --text-light: #f2f2f2;
  }
  * { box-sizing: border-box; margin: 0; padding: 0; }
  html, body {
    width: 1200px; height: 900px; overflow: hidden;
    background: var(--page-bg);
    font-family: "Montserrat", Arial, sans-serif;
  }
  .business-card {
    position: absolute;
    left: 180px; top: 208px;
    width: 840px; height: 483px;
    border-radius: 18px;
    overflow: hidden;
    background: linear-gradient(110deg, var(--card-charcoal) 0%, var(--card-black) 40%, #1a1a1a 75%, var(--card-charcoal) 100%);
    box-shadow: 0 14px 40px rgba(0,0,0,0.25);
  }
  .green-band {
    position: absolute;
    left: 0; right: 0; bottom: 0;
    height: 200px;
    background: linear-gradient(100deg, var(--brand-green) 0%, var(--brand-green-light) 45%, var(--brand-green) 100%);
  }
  .brand-lockup {
    position: absolute;
    left: 80px; top: 118px;
    display: flex; align-items: center; gap: 14px;
  }
  .brand-mark {
    width: 22px; height: 22px;
    border-radius: 50%;
    background: var(--brand-green-light);
  }
  .brand-name {
    color: var(--silver);
    font-weight: 600;
    font-size: 30px;
    letter-spacing: 0.06em;
    line-height: 1.15;
    text-transform: uppercase;
  }
  .person-block {
    position: absolute;
    right: 70px; top: 236px;
    text-align: right;
    color: var(--text-light);
  }
  .person-name {
    font-weight: 600;
    font-size: 33px;
    letter-spacing: 0.05em;
    text-transform: uppercase;
    line-height: 1;
  }
  .person-title {
    font-weight: 400;
    font-size: 19px;
    letter-spacing: 0.03em;
    margin-top: 10px;
  }
  .contact-list {
    position: absolute;
    right: 70px; top: 305px;
    list-style: none;
    color: var(--text-light);
  }
  .contact-item {
    display: flex; justify-content: flex-end; align-items: center; gap: 14px;
    font-size: 18px; letter-spacing: 0.02em;
    height: 29px;
  }
  .contact-icon { width: 15px; height: 15px; fill: var(--text-light); }
</style>
</head>
<body>
  <article class="business-card">
    <div class="green-band"></div>

    <div class="brand-lockup">
      <span class="brand-mark"></span>
      <span class="brand-name">TMW Home<br>Crafting</span>
    </div>

    <div class="person-block">
      <h1 class="person-name">Daniel Harker</h1>
      <p class="person-title">General Manager</p>
    </div>

    <ul class="contact-list">
      <li class="contact-item">0412 555 018
        <svg class="contact-icon" viewBox="0 0 16 16"><path d="M3.6 1.2 6 3.6 4.8 5.6c.8 2 2.6 3.8 4.6 4.6l2-1.2 2.4 2.4-1.6 2.4C7 13.6 2.4 9 1.2 2.8z"/></svg>
      </li>
      <li class="contact-item">info@tmwhomecrafting.com.au
        <svg class="contact-icon" viewBox="0 0 16 16"><path d="M1 3h14v10H1z M1.8 3.8 8 8.6l6.2-4.8" fill="var(--text-light)" stroke="#0f7a34" stroke-width="1.1"/></svg>
      </li>
      <li class="contact-item">tmwhomecrafting.com.au
        <svg class="contact-icon" viewBox="0 0 16 16"><circle cx="8" cy="8" r="6.5" fill="none" stroke="var(--text-light)" stroke-width="1.4"/><ellipse cx="8" cy="8" rx="2.6" ry="6.5" fill="none" stroke="var(--text-light)" stroke-width="1.2"/><path d="M1.5 8h13" stroke="var(--text-light)" stroke-width="1.2"/></svg>
      </li>
    </ul>
  </article>
</body>
</html>
```